One of a Kind Clean Business Card

We need to design a new business card template for our company. Our company designs and produced merchandising displays. You can see a sample of what we produce on our site www.qorvanexhibits.net. I have uploaded our logo in vector format, as well as a picture of our current business cards. We want a totally different look. We want simple and clean, looking forward to seeing what people create.
Updates

I would like to update the address for Qorvan Display Group Inc. 518 E Tollmere Ln Arlington Heights, IL 60017 Would also note. No QR codes

Industry/Entity Type

Business

Contact Information for Business Card

Need a 1 sided business card designed.

Font styles to use
Serif

Requirements
Must have
• Easy to view; Clean Design
Nice to have
• Features that promote engineering and creativity
Should not have
• Too much clutter, keep it simple

```html
<!DOCTYPE html>
<html lang="en">
<head>
<meta charset="utf-8">
<title>Qorvan Display Group Inc. – Business Card</title>
<link rel="stylesheet" href="https://fonts.googleapis.com/css2?family=Arimo:wght@400;700&display=swap">
<style>
  :root {
    --bg: #2a2a2a;
    --card: #ffffff;
    --brand-red: #9b1c1f;
    --ink: #2b2b2b;
    --ink-soft: #3a3a3a;
  }
  * { box-sizing: border-box; margin: 0; padding: 0; }
  html, body { width: 1200px; height: 1000px; overflow: hidden; background: var(--bg); }
  body { font-family: "Arimo", Arial, sans-serif; position: relative; }

  .card {
    position: absolute; left: 150px; top: 240px;
    width: 900px; height: 520px;
    background: var(--card);
    border-radius: 46px;
    overflow: hidden;
  }
  .card__tab {
    position: absolute; right: 0; top: 110px;
    width: 34px; height: 40px;
    background: var(--brand-red);
    border-radius: 10px 0 0 10px;
  }
  .card__waves { position: absolute; inset: 0; }

  .brand {
    position: absolute; left: 62px; top: 160px;
    font-size: 30px; font-weight: 400; color: var(--ink);
  }

  .holder-name {
    position: absolute; right: 100px; top: 150px;
    font-size: 40px; line-height: 46px; font-weight: 400; color: var(--ink);
    letter-spacing: 0.5px;
  }

  .divider {
    position: absolute; left: 160px; top: 212px;
    width: 640px; height: 2px; background: var(--brand-red);
  }

  .office {
    position: absolute; right: 100px; top: 228px;
    text-align: right; font-size: 18px; line-height: 26px; color: var(--ink-soft);
  }
  .office__company { color: var(--brand-red); font-weight: 700; }

  .contacts {
    position: absolute; left: 180px; top: 236px;
    list-style: none; font-size: 18px; line-height: 30px; color: var(--ink-soft);
  }
  .contacts li { display: flex; align-items: center; gap: 14px; }
  .contacts svg { width: 18px; height: 18px; fill: var(--brand-red); flex: none; }
  .contacts .accent { color: var(--brand-red); }
</style>
</head>
<body>
  <div class="card">
    <svg class="card__waves" viewBox="0 0 900 520" aria-hidden="true">
      <path d="M0 520 L0 505 L540 470 C610 466 630 388 710 378 L900 372 L900 520 Z" fill="var(--brand-red)"/>
      <path d="M230 478 L540 452 C585 448 600 412 640 400" fill="none" stroke="var(--brand-red)" stroke-width="6"/>
    </svg>
    <div class="card__tab"></div>

    <div class="brand">Qorvan Display Group Inc.</div>

    <div class="holder-name">DALE ORVIK</div>
    <div class="divider"></div>

    <div class="office">
      <div class="office__company">Qorvan Display Group Inc.</div>
      <div>518 E Tollmere Ln</div>
      <div>Arlington Heights, IL 60017</div>
    </div>

    <ul class="contacts">
      <li><svg viewBox="0 0 24 24"><path d="M3 8c0-2 3-4 9-4s9 2 9 4v2h-5V8H8v2H3z M6 12h12l2 8H4z"/></svg>555-201-4400</li>
      <li><svg viewBox="0 0 24 24"><path d="M6.6 10.8a15 15 0 0 0 6.6 6.6l2.2-2.2c.3-.3.7-.4 1-.2 1.1.4 2.3.6 3.6.6.6 0 1 .4 1 1V20c0 .6-.4 1-1 1A17 17 0 0 1 3 4c0-.6.4-1 1-1h3.5c.6 0 1 .4 1 1 0 1.3.2 2.5.6 3.6.1.3 0 .7-.2 1z"/></svg>555-318-0627</li>
      <li><svg viewBox="0 0 24 24"><path d="M2 5h20v14H2z M2 5l10 8 10-8" stroke="#fff" stroke-width="1.5"/></svg>dorvik@qorvanexhibits.net</li>
      <li><svg viewBox="0 0 24 24"><circle cx="14" cy="10" r="6" fill="none" stroke="var(--brand-red)" stroke-width="3"/><path d="M10 14l-7 7" stroke="var(--brand-red)" stroke-width="3"/></svg><span>www.<span class="accent">qorvanexhibits</span>.net</span></li>
    </ul>
  </div>
</body>
</html>
```